Tutoring Site Hero Image Design

Updated Hero Concept for BrightHarborLessons.com

Create a hero that communicates “high quality, in-person private tutoring for all ages,” with warmth, credibility, and a real-life feel. The hero should move away from generic stock photography and better reflect the moments that make our service different: tutors meeting students where they are, one-on-one engagement, and a range of ages.

What the New Hero Should Convey
1. In-person, private, one-on-one support
This is the core differentiator, so the visual should feel intimate, focused, and real. Avoid anything that resembles online learning settings or learning-center classrooms.

2. Coverage of age ranges without clutter
We serve elementary through college. We do not need multiple students in the hero, but the chosen student should not skew strongly to one age group. Aim for a middle-ground age that feels inclusive, for example a middle schooler or early high schooler.

3. Realistic, authentic moments
Use photography that feels candid and warm. Natural light, home settings, kitchen tables, quiet study nooks, or library corners work well. Avoid staged stock looks, harsh lighting, or exaggerated classroom setups.

Design the hero at 2400 × 1200 px, with the focal point on the right side, safe area leaving room on the left for a stacked headline and form.

Images that I've shared as just thought starters and do not need to be used in the design.

Font styles to use
Sans Serif

Colors
0054AA
0677BA
7BADD7
CADEEF
E8F1F8
EB3D1F
EC4F4E
F09395
F8D3D4
FCEDEE
6B429C
8869AF
B7A5CE
E3DAEB
F3F0F8

```html
<!DOCTYPE html>
<html lang="en">
<head>
<meta charset="utf-8">
<title>Bright Harbor Lessons – Hero Concepts</title>
<link rel="stylesheet" href="https://fonts.googleapis.com/css2?family=Poppins:wght@400;500;600;700&display=swap">
<style>
  :root{
    --navy:#1c2f86;
    --navy-deep:#0d1a66;
    --red:#e4032e;
    --pill:#e6e9f3;
    --ink:#3b3b45;
    --white:#ffffff;
    --page:#ffffff;
  }
  *{box-sizing:border-box;margin:0;padding:0}
  html,body{width:1066px;height:1200px;overflow:hidden;background:var(--page);font-family:"Poppins",sans-serif}
  .hero{position:absolute;left:80px;width:907px;height:496px;overflow:hidden;box-shadow:0 6px 24px rgba(0,0,0,.08)}
  .hero--light{top:82px;background:linear-gradient(90deg,#fff 55%,#f3f0f8 80%,#fce3e6 100%)}
  .hero--dark{top:640px;background:var(--navy-deep)}

  .photo{position:absolute}
  .hero--light .photo{left:0;top:0;width:600px;height:496px;
    background:linear-gradient(135deg,#8a6a4e 0%,#c9a277 30%,#e3b34a 55%,#d9c6a8 75%,rgba(255,255,255,0) 100%);
    -webkit-mask-image:linear-gradient(90deg,#000 75%,transparent 100%);mask-image:linear-gradient(90deg,#000 75%,transparent 100%)}
  .hero--dark .photo{left:0;top:0;width:907px;height:496px;
    background:
      linear-gradient(90deg,#0d1a66 0%,#1a2272 35%,rgba(60,40,120,.6) 55%,rgba(0,0,0,0) 75%),
      linear-gradient(160deg,#e9e2ea 0%,#e7a7ae 35%,#c96d4e 60%,#2c4a6a 80%,#e4a0a6 100%)}

  .brand{display:flex;align-items:center;gap:8px;color:var(--navy);font-weight:600;font-size:16px;line-height:1.05;white-space:nowrap}
  .brand__mark{width:26px;height:26px;background:var(--red);border-radius:4px;flex:none}
  .hero--light .brand{position:absolute;left:552px;top:32px}
  .brand-pill{position:absolute;left:0;top:34px;width:240px;height:57px;background:var(--white);border-radius:0 29px 29px 0;display:flex;align-items:center;padding-left:56px}

  .content{position:absolute;width:271px}
  .hero--light .content{left:552px;top:100px}
  .hero--dark .content{left:82px;top:148px;width:380px}

  .headline{font-weight:700;font-size:33px;line-height:37px;color:var(--navy);letter-spacing:-.2px}
  .headline .accent{color:var(--red)}
  .hero--dark .headline{color:var(--white);font-size:32px;white-space:nowrap}
  .hero--dark .headline .tag{background:var(--red);border-radius:5px;padding:0 4px}

  .intro{margin-top:14px;font-size:9.4px;line-height:17.5px;color:var(--ink);text-align:justify}
  .hero--dark .intro{color:var(--white);font-weight:500;margin-top:10px;width:350px}

  .picker{margin-top:14px;width:271px;height:84px;background:var(--white);border-radius:12px;position:relative}
  .picker__question{height:33px;border-radius:17px;border:1px solid #f5c9cf;font-size:9px;color:#666;display:flex;align-items:center;padding-left:14px;background:var(--white)}
  .picker__options{display:flex;justify-content:space-between;padding:13px 10px 0}
  .option{width:72px;height:26px;border-radius:13px;background:var(--pill);color:var(--navy);font-size:8.4px;font-weight:600;display:flex;align-items:center;justify-content:center;white-space:nowrap}
  .next{margin-top:16px;width:271px;height:33px;border-radius:17px;background:var(--red);color:var(--white);font-weight:600;font-size:11px;display:flex;align-items:center;justify-content:center}
</style>
</head>
<body>

<section class="hero hero--light">
  <div class="photo" role="img" aria-label="Photo: a smiling tutor and a teenage student working together on a laptop at a home table"></div>
  <div class="brand"><span class="brand__mark"></span><span>Bright Harbor<br>Lessons</span></div>
  <div class="content">
    <h1 class="headline">Local Tutors.<br><span class="accent">1-on-1 Learning.</span><br>Real Results.</h1>
    <p class="intro">For over 20 years, Bright Harbor Lessons has introduced students and families in our communities to experienced, professional, independent tutors who offer individualized, student-centered support across all grades and subjects, from kindergarten through college.</p>
    <div class="picker">
      <div class="picker__question">Who is being tutored?</div>
      <div class="picker__options"><span class="option">Your Child</span><span class="option">Yourself</span><span class="option">Someone else</span></div>
    </div>
    <div class="next">Next</div>
  </div>
</section>

<section class="hero hero--dark">
  <div class="photo" role="img" aria-label="Photo: a tutor leaning in beside a young student reading at a desk in warm light"></div>
  <div class="brand-pill"><div class="brand"><span class="brand__mark"></span><span>Bright Harbor<br>Lessons</span></div></div>
  <div class="content">
    <h1 class="headline">Local Tutors. <span class="tag">1-on-1</span><br>Learning.Real Results.</h1>
    <p class="intro">For over 20 years, Bright Harbor Lessons has introduced students and families in our communities to experienced, professional, independent tutors who offer individualized, student-centered support across all grades and subjects, from kindergarten through college.</p>
    <div class="picker">
      <div class="picker__question">Who is being tutored?</div>
      <div class="picker__options"><span class="option">Your Child</span><span class="option">Yourself</span><span class="option">Someone else</span></div>
    </div>
    <div class="next">Next</div>
  </div>
</section>

</body>
</html>
```